Federal IT Consulting Company - Brisolux Consulting Group

We're seeking a skilled web designer to create a modern, bold, and engaging WordPress website for Brisolux Consulting Group, LLC. Our company specializes in federal IT consulting, and our name is a play on "Brightening Solutions." The website should reflect our expertise in the federal technology marketplace and position us as a trusted partner for clients navigating their IT journey.

contact: info@brisoluxgrp-example.com

Current Status

WordPress is already installed on our hosting account
We have an existing logo (may need modernization)

Design Requirements

Style:

Modern and visually striking design
Bold elements to convey confidence and expertise
Incorporate the concept of "brightening solutions" into the design

Features:

Modern UX sliders for dynamic content presentation
Eye-catching, high-quality images (stock photos to be sourced by the designer)
Responsive design for all devices

Color Scheme:

To be proposed by the designer, should align with our brand and convey trust and technological expertise

Logo:

Evaluate our current logo
Create a transparent background version if needed
Propose modernization if deemed necessary

Accessibility:

Ensure design elements are accessible to users with disabilities
Use high contrast ratios for text and background colors
Provide text alternatives for non-text content

Website Structure
Create the following pages, with the possibility of subpages:

Home
Services
About
Contact

Specific Page Requirements
Home Page

Striking hero section with a clear value proposition
Overview of our services
Client testimonials or trust indicators

Services Page

Detailed list of our IT consulting services
Clear explanation of how we help navigate the federal IT landscape

About Page

Company history and mission
Team highlights (if applicable)
Our approach to federal IT consulting

Contact Page

Contact form
Other contact methods (phone, email)

Technical Requirements

Fully responsive design
SEO best practices implemented
Fast loading times
Integration with necessary plugins (to be discussed)
Training on how to update and maintain the site
Full compliance with Web Content Accessibility Guidelines (WCAG) 2.1 Level AA
Adherence to Section 508 standards for federal website accessibility
Implementation of necessary features for ADA compliance
Updates

Designs look the same

Target Market(s)

US Federal Govt customers looking for IT support.

Industry/Entity Type

IT Consulting

Coding

Coded - Design and coding required

Colors
0054AA
0677BA
7BADD7
CADEEF
E8F1F8
0094D4
00A9DD
6FCCEA
C7EBF8
E9F6FB
00AB8E
00BBA5
67D7C9
C6EFE9
E9F9F6

```html
<!DOCTYPE html>
<html lang="en">
<head>
<meta charset="utf-8">
<title>Brisolux Federal Services</title>
<link href="https://fonts.googleapis.com/css2?family=Lato:wght@400;700&family=Roboto:wght@400;500;700&display=swap" rel="stylesheet">
<style>
:root{
  --accent:#0aa6de;
  --accent-deep:#0677ba;
  --ink:#333335;
  --text:#4a4a4c;
  --muted:#6b6b6e;
  --hero-bg:#eef7fb;
  --line:#e3e8ec;
  --dark:#3f3f41;
  --dark-card:#3d3d3f;
  --white:#ffffff;
}
*{margin:0;padding:0;box-sizing:border-box}
html,body{width:1200px;height:3062px;overflow:hidden;background:var(--white)}
body{position:relative;font-family:"Lato",sans-serif;color:var(--text)}
.abs{position:absolute}
.head-font{font-family:"Roboto",sans-serif}
.btn{position:absolute;display:flex;align-items:center;justify-content:center;background:var(--accent);color:var(--white);border-radius:22px;font-family:"Roboto",sans-serif;font-size:16px}

/* header */
.brand{display:flex;align-items:center;gap:12px}
.brand-dot{width:46px;height:46px;border-radius:50%;background:var(--accent)}
.brand-name{font-family:"Roboto",sans-serif;font-weight:700;font-size:40px;color:var(--ink);letter-spacing:1px}
.nav a{position:absolute;top:47px;font-family:"Roboto",sans-serif;font-size:16px;color:#555;text-decoration:none}

/* hero */
.hero{left:0;top:112px;width:1200px;height:564px;background:var(--hero-bg)}
.hero-photo{left:600px;top:112px;width:600px;height:564px;background:linear-gradient(135deg,#c9d6de 0%,#e6ecef 45%,#b9c2c6 75%,#dfe5e8 100%)}
.welcome{left:112px;top:214px;font-family:"Roboto",sans-serif;font-size:26px;color:var(--ink)}
.hero-title{left:110px;top:264px;font-family:"Roboto",sans-serif;font-weight:700;font-size:57px;line-height:68px;color:var(--ink)}
.hero-title span,.hl{color:var(--accent)}
.hero-text{left:112px;top:415px;width:420px;font-size:18px;line-height:27px;color:var(--text)}

/* services */
.section-title{left:0;width:1200px;text-align:center;font-family:"Roboto",sans-serif;font-weight:700;font-size:45px;color:var(--ink)}
.hub{left:419px;top:901px;width:362px;height:362px;border-radius:50%;background:radial-gradient(circle at 50% 40%,#b8c2c8 0%,#5c6874 55%,#2e3640 100%)}
.card{position:absolute;width:258px;height:125px;border:1px solid var(--line);border-radius:16px;background:var(--white);padding:24px 24px 0}
.card.left{border-top-right-radius:0;border-bottom-right-radius:0;border-right-color:#eef1f3}
.card.right{border-top-left-radius:0;border-bottom-left-radius:0;padding-left:44px}
.card h3{font-family:"Roboto",sans-serif;font-weight:400;font-size:22px;color:var(--ink);margin-bottom:10px}
.card p{font-size:15.5px;line-height:20px;color:var(--text)}
.card.active{background:var(--dark-card);border-color:var(--dark-card)}
.card.active h3{color:var(--accent)}
.card.active p{color:var(--white)}
.badge{position:absolute;width:70px;height:75px;background:var(--accent);border-radius:10px;display:flex;align-items:center;justify-content:center;font-family:"Roboto",sans-serif;font-weight:500;font-size:26px;color:var(--white)}
.badge.left{border-top-left-radius:0;border-bottom-left-radius:14px}
.badge.right{border-top-right-radius:0}
.badge::before{content:"";position:absolute;top:0;width:14px;height:14px;background:var(--accent-deep)}
.badge.left::before{left:-14px;border-top-left-radius:14px}
.badge.right::before{right:-14px;border-top-right-radius:14px}

/* about */
.about-photo{left:112px;top:1421px;width:478px;height:566px;border-radius:20px;background:linear-gradient(160deg,#c8a676 0%,#e9eef1 40%,#8aa3b4 75%,#5d5148 100%)}
.about-title{left:686px;top:1422px;font-family:"Roboto",sans-serif;font-weight:700;font-size:46px;color:var(--ink)}
.about-sub{left:684px;top:1488px;font-size:20px;color:var(--text)}
.tabs{left:683px;top:1541px;width:405px;height:52px;border-radius:26px;background:#eef7fb}
.tab{position:absolute;top:17px;font-family:"Roboto",sans-serif;font-size:16px;font-weight:500;color:var(--ink)}
.tab.on{color:var(--accent)}
.tab-line{position:absolute;left:35px;top:26px;width:47px;height:2px;background:var(--accent)}
.about-text{left:686px;width:400px;font-size:15.5px;line-height:21.5px;color:var(--text)}

/* testimonials */
.quote{position:absolute;top:2162px;width:290px}
.avatar{position:absolute;left:0;top:0;width:76px;height:76px;border-radius:8px}
.q-name{position:absolute;left:96px;top:6px;font-family:"Roboto",sans-serif;font-size:18px;color:var(--accent)}
.q-date{position:absolute;left:96px;top:36px;font-size:12px;color:var(--muted)}
.q-mark{position:absolute;left:96px;top:52px;font-family:"Roboto",sans-serif;font-weight:700;font-size:34px;color:#e8b53a;line-height:1}
.q-text{position:absolute;left:0;top:96px;width:270px;font-size:15.5px;line-height:22px;color:var(--text)}
.dot{position:absolute;top:2365px;height:7px;border-radius:2px;background:#cfd3d6}

/* footer */
.footer{left:0;top:2460px;width:1200px;height:547px;background:var(--dark)}
.footer .brand-name{color:var(--white)}
.footer .brand-dot{background:var(--white)}
.vrule{left:439px;top:2501px;width:1px;height:110px;background:#8a8a8c}
.news-title{left:484px;top:2519px;font-family:"Roboto",sans-serif;font-weight:700;font-size:25px;color:var(--white)}
.news-text{left:484px;top:2554px;font-family:"Roboto",sans-serif;font-weight:500;font-size:13px;line-height:20px;color:var(--white)}
.email{left:714px;top:2540px;width:239px;height:45px;border:1px solid #cfcfcf;border-radius:23px;padding-left:18px;display:flex;align-items:center;font-size:13px;color:var(--white)}
.email svg{position:absolute;right:16px;top:16px}
.hrule{left:112px;top:2658px;width:976px;height:1px;background:#5c5c5e}
.col-head{position:absolute;top:2716px;font-family:"Roboto",sans-serif;font-weight:700;font-size:20px;color:var(--white)}
.col-head::after{content:"";position:absolute;left:0;top:36px;width:86px;height:2px;background:var(--accent)}
.col-head i{position:absolute;left:82px;top:33px;width:7px;height:7px;border-radius:50%;background:var(--accent)}
.foot-text{left:112px;top:2776px;width:240px;font-size:15.5px;line-height:22px;color:var(--white)}
.social{position:absolute;top:2888px;width:34px;height:34px;border-radius:50%;background:var(--accent)}
.links{position:absolute;top:2776px;list-style:none}
.links li{height:36px;font-size:15.5px;color:var(--white);padding-left:26px;position:relative}
.links li::before{content:"";position:absolute;left:2px;top:7px;width:6px;height:6px;border-right:1.5px solid var(--white);border-top:1.5px solid var(--white);transform:rotate(45deg)}
.post-thumb{position:absolute;left:859px;width:68px;height:67px;border-radius:4px;background:linear-gradient(135deg,#d7e0e6,#7e96a8)}
.post-title{position:absolute;left:938px;width:160px;font-family:"Roboto",sans-serif;font-weight:700;font-size:15.5px;line-height:23px;color:var(--white)}
.post-date{position:absolute;left:938px;font-size:13px;color:var(--white);display:flex;align-items:center;gap:6px}
.post-date b{width:9px;height:9px;background:var(--accent);border-radius:1px}
.copy{left:0;top:3007px;width:1200px;height:55px;background:var(--accent);display:flex;align-items:center;justify-content:center;font-size:14px;color:var(--white)}
</style>
</head>
<body>

<!-- header -->
<header>
  <div class="abs brand" style="left:113px;top:32px">
    <span class="brand-dot"></span><span class="brand-name">BRISOLUX</span>
  </div>
  <nav class="nav">
    <a style="left:543px">Home</a>
    <a style="left:634px">Services</a>
    <a style="left:742px">About</a>
    <a style="left:833px">Contact</a>
  </nav>
  <a class="btn" style="left:934px;top:34px;width:153px;height:43px">Get Started</a>
</header>

<!-- hero -->
<section>
  <div class="abs hero"></div>
  <div class="abs hero-photo" role="img" aria-label="Photo of a consulting team reviewing work on a laptop in a bright office"></div>
  <p class="abs welcome">Welcome To</p>
  <h1 class="abs hero-title"><span>Brisolux</span> Federal<br>Services</h1>
  <p class="abs hero-text">Lorem ipsum dolor sit amet, consectetur adipiscing elit, sed do eiusmod tempor incididunt ut labore et dolore magna aliqua.</p>
  <a class="btn" style="left:112px;top:524px;width:153px;height:43px">Contact Us</a>
</section>

<!-- services -->
<section>
  <h2 class="abs section-title" style="top:750px">Our <span class="hl">Services</span></h2>
  <div class="abs hub" role="img" aria-label="Photo of two consultants discussing a tablet"></div>

  <div class="card left" style="left:151px;top:865px"><h3>Lorem ipsum dolor</h3><p>Excepteur sint&nbsp; non culpa qui mollit anim id est laborum.</p></div>
  <div class="badge left" style="left:365px;top:849px">04</div>

  <div class="card left" style="left:113px;top:1028px"><h3>Lorem ipsum dolor</h3><p>Excepteur sint&nbsp; non culpa qui mollit anim id est laborum.</p></div>
  <div class="badge left" style="left:327px;top:1012px">05</div>

  <div class="card left" style="left:151px;top:1190px"><h3>Lorem ipsum dolor</h3><p>Excepteur sint&nbsp; non culpa qui mollit anim id est laborum.</p></div>
  <div class="badge left" style="left:365px;top:1175px">06</div>

  <div class="card right" style="left:789px;top:865px"><h3>Lorem ipsum dolor</h3><p>Excepteur sint&nbsp; non culpa qui mollit anim id est laborum.</p></div>
  <div class="badge right" style="left:763px;top:849px">01</div>

  <div class="card right" style="left:827px;top:1028px"><h3>Lorem ipsum dolor</h3><p>Excepteur sint&nbsp; non culpa qui mollit anim id est laborum.</p></div>
  <div class="badge right" style="left:802px;top:1012px">02</div>

  <div class="card right active" style="left:789px;top:1190px"><h3>Lorem ipsum dolor</h3><p>Excepteur sint&nbsp; non culpa qui mollit anim id est laborum.</p></div>
  <div class="badge right" style="left:763px;top:1175px">03</div>
</section>

<!-- about -->
<section>
  <div class="abs about-photo" role="img" aria-label="Photo of two colleagues working at a laptop in front of a chart wall"></div>
  <h2 class="abs about-title">About <span class="hl">Us</span></h2>
  <p class="abs about-sub">Excepteur sint occaecat cupidatat non</p>
  <div class="abs tabs">
    <span class="tab-line"></span>
    <span class="tab on" style="left:90px">About</span>
    <span class="tab" style="left:174px">Mission</span>
    <span class="tab" style="left:277px">Our Approach</span>
  </div>
  <p class="abs about-text" style="top:1634px">Lorem ipsum dolor sit amet, consectetur adipiscing elit, sed do eiusmod tempor incididunt ut labore et dolore magna aliqua. Ut enim ad minim veniam, quis nostrud exercitation Excepteur sint occaecat cupidatat non proident, sunt in culpa quiullamco laboris nisi ut aliquip ex ea commodo</p>
  <p class="abs about-text" style="top:1769px">Sed ut perspiciatis unde omnis iste natus error sit volupt accusantium doloremque laudantium, totam rem aperiam, eaque ipsa quae ab illo inventore veritatis et quasi archite beatae vitae dicta sunt explicabo. Nemo enim ipsam volupt quia voluptas sit magni dolores eos qui ratione voluptatem sequi nesciunt.</p>
  <a class="btn" style="left:684px;top:1939px;width:155px;height:42px">Read More</a>
</section>

<!-- testimonials -->
<section>
  <h2 class="abs section-title" style="top:2065px">Our <span class="hl">Testimonials</span></h2>

  <div class="quote" style="left:112px">
    <div class="avatar" role="img" aria-label="Portrait of a client" style="background:linear-gradient(160deg,#b9a58c,#2f5246)"></div>
    <span class="q-name">Lorem ipsum</span><span class="q-date">Date : 09/07/2024</span><span class="q-mark">&ldquo;</span>
    <p class="q-text">Excepteur sint occaecat cupidatat non proident, sunt in culpa qui officia dese runt mollit anim id est laborum."</p>
  </div>
  <div class="quote" style="left:472px">
    <div class="avatar" role="img" aria-label="Portrait of a client" style="background:linear-gradient(160deg,#d9c7a8,#c9a227)"></div>
    <span class="q-name">Lorem ipsum</span><span class="q-date">Date : 09/07/2024</span><span class="q-mark">&ldquo;</span>
    <p class="q-text">Excepteur sint occaecat cupidatat non proident, sunt in culpa qui officia dese runt mollit anim id est laborum."</p>
  </div>
  <div class="quote" style="left:832px">
    <div class="avatar" role="img" aria-label="Portrait of a client" style="background:linear-gradient(160deg,#bfe0ea,#f2f4f5)"></div>
    <span class="q-name">Lorem ipsum</span><span class="q-date">Date : 09/07/2024</span><span class="q-mark">&ldquo;</span>
    <p class="q-text">Excepteur sint occaecat cupidatat non proident, sunt in culpa qui officia dese runt mollit anim id est laborum."</p>
  </div>

  <span class="dot" style="left:561px;width:28px;background:var(--accent)"></span>
  <span class="dot" style="left:595px;width:19px"></span>
  <span class="dot" style="left:621px;width:19px"></span>
</section>

<!-- footer -->
<footer>
  <div class="abs footer"></div>
  <div class="abs brand" style="left:109px;top:2532px">
    <span class="brand-dot"></span><span class="brand-name">BRISOLUX</span>
  </div>
  <div class="abs vrule"></div>
  <h3 class="abs news-title">News Subscription</h3>
  <p class="abs news-text">Get Latest Deals from Halden's<br>Inbox &amp; Subscribe Now</p>
  <div class="abs email">Email Address
    <svg width="14" height="11" viewBox="0 0 14 11" fill="none" stroke="#0aa6de" stroke-width="1.4"><rect x="1" y="1" width="12" height="9" rx="1"/><path d="M1 1.5l6 4.5 6-4.5"/></svg>
  </div>
  <a class="btn" style="left:966px;top:2540px;width:122px;height:45px;font-size:17px">Subscribe</a>
  <div class="abs hrule"></div>

  <h4 class="col-head" style="left:112px">About Company<i></i></h4>
  <h4 class="col-head" style="left:396px">Quick Links<i></i></h4>
  <h4 class="col-head" style="left:613px">Other Links<i></i></h4>
  <h4 class="col-head" style="left:858px">Recent Posts<i></i></h4>

  <p class="abs foot-text">Lorem ipsum dolor sit amet, consectetur adipiscing elit, sed do eiusmod tempor incididunt ut labore et dolore magna aliqua.</p>
  <span class="social" style="left:111px" role="img" aria-label="Social profile link"></span>
  <span class="social" style="left:155px" role="img" aria-label="Social profile link"></span>
  <span class="social" style="left:199px" role="img" aria-label="Social profile link"></span>

  <ul class="links" style="left:396px"><li>Home</li><li>Services</li><li>About</li><li>Contact</li></ul>
  <ul class="links" style="left:613px"><li>Support</li><li>Terms and Conditions</li><li>Privacy Policy</li><li>Cookies Policy</li></ul>

  <div class="post-thumb" style="top:2779px" role="img" aria-label="Thumbnail photo for a blog post"></div>
  <p class="post-title" style="top:2778px">Lorem ipsum dolor sit amet, consectetur</p>
  <span class="post-date" style="top:2830px"><b></b>July 09 2024</span>
  <div class="post-thumb" style="top:2868px" role="img" aria-label="Thumbnail photo for a blog post"></div>
  <p class="post-title" style="top:2867px">Lorem ipsum dolor sit amet, consectetur</p>
  <span class="post-date" style="top:2919px"><b></b>July 09 2024</span>

  <div class="abs copy">Copyright © 2024 Brisolux Federal Services. All rights reserved.</div>
</footer>

</body>
</html>
```